We are a Machine Engineering Company based in Singapore since 1978. We supply tools & machine accessories to Manufacturing Plants using CNC Machines.

We sell Drills / Taps / Reamers / Carbide & Ceramic Inserts / Arbors / Chucks / Vise / etc...

We need an E Christmas Card to send out to our customers Worldwide.
It should have our Company Logo.
It should also include Greetings for the New Year.

Target Market(s)

Manufacturers of Aero Space / Oil & Gas / Automotive / Medical Science / etc

Requirements
Must have
• Company Logo
• Link : www.halvorn.com.sg
Nice to have
• Modern Designs
Should not have
• Porn or Suggestive Pictures.

```html
<!DOCTYPE html>
<html lang="en">
<head>
<meta charset="utf-8">
<title>Halvorn Tools – Season's Greetings</title>
<link rel="stylesheet" href="https://fonts.googleapis.com/css2?family=Amatic+SC:wght@400;700&display=swap">
<style>
  :root {
    --crimson: #93003a;
    --crimson-deep: #7a0030;
    --gold: #c9a94a;
    --ink: #3a0d1e;
    --paper: #ffffff;
    --frame: #c8c8c8;
    --garland-tint: #f6eef1;
  }
  html, body {
    margin: 0;
    padding: 0;
    width: 1200px;
    height: 1197px;
    overflow: hidden;
    background: var(--paper);
  }
  .card {
    position: relative;
    width: 1200px;
    height: 1197px;
    background: var(--paper);
    font-family: "Amatic SC", "Arial Narrow", sans-serif;
  }
  .card__frame {
    position: absolute;
    left: 30px; top: 20px;
    width: 1138px; height: 1137px;
    border: 2px solid var(--frame);
  }
  .card__art {
    position: absolute;
    left: 0; top: 0;
    width: 1200px; height: 1197px;
  }
  .greeting {
    position: absolute;
    margin: 0;
    font-weight: 400;
    line-height: 1;
    text-align: center;
    white-space: nowrap;
    text-transform: uppercase;
  }
  .greeting--merry {
    left: 213px; width: 300px; top: 283px;
    font-size: 100px;
    color: var(--paper);
    letter-spacing: 2px;
  }
  .greeting--christmas {
    left: 163px; width: 400px; top: 385px;
    font-size: 112px;
    color: var(--paper);
    letter-spacing: 0;
  }
  .greeting--happy {
    left: 763px; width: 300px; top: 308px;
    font-size: 70px;
    color: var(--crimson);
    letter-spacing: 5px;
  }
  .greeting--newyear {
    left: 712px; width: 420px; top: 371px;
    font-size: 129px;
    color: var(--crimson);
    letter-spacing: 3px;
  }
  .brand {
    position: absolute;
    left: 753px; top: 1020px;
    width: 324px;
    display: flex;
    flex-direction: column;
    align-items: center;
    gap: 10px;
  }
  .brand__row {
    display: flex;
    align-items: center;
    gap: 12px;
  }
  .brand__dot {
    width: 26px; height: 26px;
    border-radius: 50%;
    background: var(--crimson);
    flex: none;
  }
  .brand__name {
    font-size: 56px;
    font-weight: 700;
    color: var(--crimson);
    line-height: 1;
    white-space: nowrap;
    text-transform: uppercase;
  }
  .brand__link {
    font-size: 32px;
    font-weight: 700;
    color: var(--crimson);
    line-height: 1;
    letter-spacing: 2px;
    text-decoration: none;
    white-space: nowrap;
  }
</style>
</head>
<body>
<main class="card">
  <svg class="card__art" viewBox="0 0 1200 1197" xmlns="http://www.w3.org/2000/svg">
    <rect class="panel" x="33" y="23" width="633" height="975" fill="var(--crimson)"/>
    <rect class="panel__snowfall" x="33" y="23" width="633" height="660" fill="var(--crimson)" opacity="0.95"
          role="img" aria-label="Falling snow flecks scattered over the crimson panel"/>
    <rect class="panel__trees" x="197" y="707" width="255" height="270" rx="60" fill="#b8527a" opacity="0.55"
          role="img" aria-label="Two white fir trees with gold baubles"/>
    <path class="hills" d="M33 978 Q220 940 430 975 Q520 940 666 935 L666 1155 L33 1155 Z" fill="var(--paper)"/>
    <path class="hills__edge" d="M33 978 Q220 940 430 975" fill="none" stroke="var(--crimson-deep)" stroke-width="6" opacity="0.6"/>

    <rect class="garland" x="674" y="130" width="494" height="80" rx="40" fill="var(--garland-tint)"
          role="img" aria-label="Looping string garland"/>
    <rect class="garland" x="674" y="575" width="494" height="75" rx="37" fill="var(--garland-tint)"
          role="img" aria-label="Looping string garland"/>
    <rect class="garland" x="674" y="755" width="494" height="75" rx="37" fill="var(--garland-tint)"
          role="img" aria-label="Looping string garland"/>

    <g class="baubles">
      <circle cx="718" cy="110" r="16" fill="var(--crimson)"/>
      <circle cx="1097" cy="164" r="26" fill="var(--crimson)"/>
      <circle cx="751" cy="587" r="43" fill="var(--crimson)"/>
      <circle cx="937" cy="779" r="33" fill="var(--crimson)"/>
      <circle cx="884" cy="543" r="13" fill="var(--gold)"/>
      <circle cx="1110" cy="715" r="16" fill="var(--gold)"/>
      <circle cx="1077" cy="830" r="21" fill="var(--gold)"/>
      <circle cx="718" cy="917" r="16" fill="var(--gold)"/>
    </g>

    <g class="sparkles" fill="var(--gold)">
      <path d="M863 170 l5 15 l15 5 l-15 5 l-5 15 l-5 -15 l-15 -5 l15 -5 Z"/>
      <path d="M1113 560 l4 14 l14 4 l-14 4 l-4 14 l-4 -14 l-14 -4 l14 -4 Z"/>
      <path d="M770 722 l6 19 l19 6 l-19 6 l-6 19 l-6 -19 l-19 -6 l19 -6 Z"/>
      <path d="M1090 910 l3 11 l11 3 l-11 3 l-3 11 l-3 -11 l-11 -3 l11 -3 Z"/>
    </g>
  </svg>

  <div class="card__frame"></div>

  <h1 class="greeting greeting--merry">Merry</h1>
  <h1 class="greeting greeting--christmas">Christmas</h1>
  <h2 class="greeting greeting--happy">&amp; Happy</h2>
  <h2 class="greeting greeting--newyear">New Year</h2>

  <div class="brand">
    <div class="brand__row">
      <span class="brand__dot"></span>
      <span class="brand__name">Halvorn Tools</span>
    </div>
    <a class="brand__link" href="https://www.halvorn.com.sg">www.halvorn.com.sg</a>
  </div>
</main>
</body>
</html>
```